SEO Agentur www.klickretter.de - Webseite soll neu designed werden (Start- und Unterseite)
Zielgruppe
Alle Infos sind auf der Seite www.klickretter.de enthalten.
Aufgabenstellung
Die Seite soll neu gestalltet werden. Wir möchten gerne ein wenig professioneller werden. Der Name der Seite zwingt uns allerdings ein gewisses Thema auf.
Die Aufgabe:
Ein professionelleres Design der Startseite und einer Unterseite. Die Programmierung machen wir selbst. Thema Suche und Helden muss bleiben aufgrund der URL.
Mit dem Gewinner würden wir dann auch geren jedes Element der Seite durchgehen und neu gestallten (separater Auftrag).
Das Blitzwolf Logo ist aufgrund des neuen Films auch gewaltiger und seriöser geworden. Vielleicht kann man daran anknüpfen. Ist aber keine Bedingung nur eine kleine Idee.
Wir werden alle Vorschläge ca. 50 Leuten vorstellen und dann den Vorschlag mit den meisten Stimmen wählen.

```html
<!DOCTYPE html>
<html lang="de">
<head>
<meta charset="utf-8">
<title>Klickretter – SEO Agentur</title>
<link href="https://fonts.googleapis.com/css2?family=Oswald:wght@400;500;600&family=Mulish:ital,wght@0,400;0,600;1,400&display=swap" rel="stylesheet">
<style>
:root{
  --red:#d9270f;
  --red-dark:#b81f0b;
  --ink:#2b2b2b;
  --text:#666;
  --dark:#2e2e2e;
  --darker:#262626;
  --light:#f5f5f5;
  --rule:#e2e2e2;
  --track:#e6e6e6;
}
*{margin:0;padding:0;box-sizing:border-box}
html,body{width:708px;height:1200px;overflow:hidden;background:#fff}
body{position:relative;font-family:"Mulish",sans-serif;color:var(--text)}
.abs{position:absolute}
.h{font-family:"Oswald",sans-serif;text-transform:uppercase;color:var(--ink);font-weight:500;letter-spacing:-.2px}

.topbar{left:0;top:0;width:708px;height:16px;background:var(--red);color:#fff;font-size:3.8px;font-weight:600}
.topbar span{position:absolute;top:5.5px}
.header{left:0;top:16px;width:708px;height:43px;background:linear-gradient(#fff,#eee);border-bottom:1px solid #ddd}
.brand{left:142px;top:11px;display:flex;align-items:center;gap:3px}
.brand .dot{width:12px;height:12px;border-radius:50%;background:var(--red)}
.brand .name{font-family:"Oswald",sans-serif;font-weight:500;font-size:9.5px;color:var(--ink)}
.tagline{left:142px;top:24px;font-size:3.4px;color:#999;letter-spacing:.2px}
.nav{left:245px;top:18px;width:316px;display:flex;justify-content:space-between;font-family:"Oswald",sans-serif;font-size:6.3px;color:#555;text-transform:uppercase}
.nav .on{color:var(--red)}

.hero{left:0;top:59px;width:708px;height:210px;background:linear-gradient(90deg,#3a3a3a,#6f6f6f 50%,#3a3a3a)}
.hero-band{left:0;top:96px;width:708px;height:136px;background:rgba(30,30,30,.72)}
.hero-bottom{left:0;top:269px;width:708px;height:2px;background:#ddd}
.thumb{left:335px;top:77px;width:38px;height:38px;border-radius:50%;background:var(--red);display:flex;align-items:center;justify-content:center}
.hero-title{left:0;top:134px;width:708px;text-align:center;font-family:"Oswald",sans-serif;font-size:27px;font-weight:500;color:#fff;letter-spacing:-.5px}
.hero-sub{left:0;top:169px;width:708px;text-align:center;font-size:9.5px;color:#fff}

.about h2{font-size:10.5px}
.small{font-size:4.9px;line-height:7.4px}
.socials{display:flex;gap:4.5px}
.socials i{width:9px;height:9px;border-radius:50%;border:.6px solid #ccc;display:block;background:#fafafa}
.bar{left:360px;width:206px;height:14px;background:var(--track)}
.bar .fill{height:100%;background:linear-gradient(var(--red),var(--red-dark));clip-path:polygon(0 0,100% 0,calc(100% - 6px) 100%,0 100%);position:relative;color:#fff;font-family:"Oswald",sans-serif;font-size:5.4px;line-height:14px}
.bar .fill b{font-weight:500;position:absolute;left:8px}
.bar .fill em{font-style:normal;position:absolute;right:9px;font-size:4.6px}

.svc-icon{width:27px;height:27px;border-radius:50%;background:var(--red);box-shadow:0 0 0 2px #eee;display:flex;align-items:center;justify-content:center}
.svc h3{font-size:6.6px;margin-bottom:3px}
.svc p{font-size:4.9px;line-height:7.4px;width:95px}
.svc a{color:var(--red);text-decoration:none}

.cta{left:0;top:624px;width:708px;height:102px;background:var(--dark);text-align:center}
.cta h2{color:#fff;font-size:12.5px;margin-top:29px}
.cta p{font-size:4.9px;line-height:7.4px;color:#bbb;margin-top:6px}

.col h2{font-size:7px;font-weight:400}
.col h2 strong{font-size:10.5px;font-weight:600}
.col ul{list-style:none;margin-top:6px}
.col li{font-size:4.9px;line-height:10.4px;padding-left:7px;position:relative}
.col li::before{content:"";position:absolute;left:0;top:3.5px;border:1.6px solid transparent;border-left:2.4px solid var(--red)}
.btn{display:inline-block;background:var(--red);color:#fff;font-family:"Oswald",sans-serif;font-size:5.3px;width:52px;height:17px;line-height:17px;text-align:center;text-transform:uppercase;border-radius:1px}

.quote{left:0;top:929px;width:708px;height:134px;background:var(--light);border-top:1px solid #e8e8e8;text-align:center}
.quote blockquote{font-style:italic;font-size:7.8px;line-height:13.4px;color:#666;margin:42px auto 0;width:360px}
.quote cite{display:block;font-style:normal;font-size:5.6px;color:#aaa;margin-top:10px}
.dots{display:flex;justify-content:center;gap:5px;margin-top:12px;align-items:center}
.dots i{width:4.5px;height:4.5px;border-radius:50%;background:#bbb}
.dots i.on{width:6.5px;height:6.5px;background:var(--red)}

.footer{left:0;top:1063px;width:708px;height:113px;background:var(--dark);color:#bbb}
.footer h4{font-family:"Oswald",sans-serif;font-size:6px;font-weight:500;color:#fff;text-transform:uppercase}
.flinks{list-style:none;width:97px;margin-top:6px}
.flinks li{font-size:4.9px;color:#fff;border-bottom:.6px solid #444;padding:4.5px 0 4.5px 7px}
.ftext{font-size:4.9px;line-height:7.4px;color:#aaa}
.contact-row{display:flex;gap:9px;font-size:4.9px;line-height:7.2px;color:#bbb}
.contact-row .ic{width:12px;height:12px;border-radius:50%;background:#3a3a3a;flex:none;display:flex;align-items:center;justify-content:center}
.bottombar{left:0;top:1176px;width:708px;height:24px;background:var(--darker);font-size:4.2px;color:#bbb}
.bottombar .fsoc i{width:9px;height:9px;border-radius:50%;background:#3d3d3d;display:block}
</style>
</head>
<body>

<div class="abs topbar">
  <span style="left:142px">☎ HOTLINE +49 (30) 555 019 42</span>
  <span style="left:213px">✉ INFO@KLICKRETTER.DE</span>
  <span style="left:494px">♥ WIR FREUEN UNS AUF SIE</span>
</div>

<header class="abs header">
  <div class="abs brand"><span class="dot"></span><span class="name">KLICKRETTER</span></div>
  <div class="abs tagline">WIR FINDEN IHREN TRAFFIC</div>
  <nav class="abs nav">
    <span class="on">Home</span><span>Ihre Vorteile</span><span>Unsere Leistungen ▾</span><span>100% Geld-Zurück-Garantie</span><span>Infos</span><span>Blog</span><span>Kontakt</span>
  </nav>
</header>

<section class="abs hero" role="img" aria-label="Foto: Mann im Anzug reißt sein Hemd auf"></section>
<div class="abs hero-band"></div>
<div class="abs hero-bottom"></div>
<div class="abs thumb">
  <svg width="17" height="17" viewBox="0 0 24 24" fill="none" stroke="#fff" stroke-width="2" stroke-linejoin="round"><path d="M7 10v11H3V10zM7 10l4-8c2 0 3 1 3 3v3h6c1.2 0 2 1 1.8 2.2l-1.6 8c-.2 1-1 1.8-2 1.8H7"/></svg>
</div>
<h1 class="abs hero-title">GELD ZURÜCK GARANTIE!</h1>
<p class="abs hero-sub">Lorem ipsum dolor sit amet consectetur adipiscing elit.</p>

<section class="about">
  <h2 class="abs h" style="left:142px;top:292px">SEO Agentur Klickretter</h2>
  <h3 class="abs h" style="left:142px;top:309px;font-size:6.4px">Erfolgsbasiert und mit 100% Geld zurück Garantie</h3>
  <p class="abs small" style="left:142px;top:322px;width:206px">Lorem ipsum dolor sit amet, consectetur adipiscing elit. Sed placerat luctus leo, eget luctus nisi porttitor in. Morbi ac adipiscing nisi, nec lacinia felis. Morbi ornare lacus varius dolor commodo tempor non fermentum est sodales eget.</p>
  <p class="abs small" style="left:142px;top:352px;width:206px">Mauris varius metus at porttitor laoreet. Nulla venenatis condimentum tortor, in cursus arcu fringilla eu. Morbi luctus, lacus rutrum porta adipiscing, lectus enim congue justo, in suscipit justo nunc congue mauris Mauris est libero, sagittis sed adipiscing et, convallis dapibus ante. Morbi ac adipiscing nisi, nec.</p>
  <div class="abs socials" style="left:144px;top:389px"><i></i><i></i><i></i><i></i><i></i></div>

  <h2 class="abs h" style="left:360px;top:292px;font-size:7.6px">Unsere Superkräfte</h2>
  <div class="abs bar" style="top:309px"><div class="fill" style="width:99%"><b>SEO</b><em>99%</em></div></div>
  <div class="abs bar" style="top:330px"><div class="fill" style="width:97%"><b>Konzeption</b><em>97%</em></div></div>
  <div class="abs bar" style="top:350px"><div class="fill" style="width:82%"><b>Design</b><em>82%</em></div></div>
  <div class="abs bar" style="top:371px"><div class="fill" style="width:89%"><b>Videos</b><em>89%</em></div></div>
</section>

<div class="abs" style="left:142px;top:420px;width:424px;height:1px;background:var(--rule)"></div>
<h2 class="abs h" style="left:0;top:441px;width:708px;text-align:center;font-size:11.5px">Was bieten wir Ihnen sonst noch?</h2>

<div class="abs svc-icon" style="left:142px;top:475px"><svg width="11" height="11" viewBox="0 0 24 24" fill="#fff"><path d="M21 3c-6 0-10 3-13 8l-4 1 3 2 3 3 2 3 1-4c5-3 8-7 8-13zM5 16c-2 1-2 4-2 5 1 0 4 0 5-2z"/></svg></div>
<div class="abs svc" style="left:179px;top:478px"><h3 class="h">Suchmaschinenoptimierung</h3><p>Lorem ipsum dolor sit amet, consectetur adipiscing elit. Praesent eu nisi ac mi Ut egestas libero sit amet risus elementum rhoncus, elit id varius. <a>Mehr erfahren</a></p></div>
<div class="abs svc-icon" style="left:287px;top:475px"><svg width="11" height="11" viewBox="0 0 24 24" fill="#fff"><path d="M2 4h20v13H2zM9 19h6v2H9z"/><path d="M4 6h16v9H4z" fill="var(--red)"/></svg></div>
<div class="abs svc" style="left:324px;top:478px"><h3 class="h">Homepageerstellung</h3><p>Lorem ipsum dolor sit amet, consectetur adipiscing elit. Praesent eu nisi ac mi Ut egestas libero sit amet risus elementum rhoncus, elit id varius. <a>Mehr erfahren</a></p></div>
<div class="abs svc-icon" style="left:432px;top:475px"><svg width="11" height="11" viewBox="0 0 24 24" fill="#fff"><path d="M3 9h4l10-5v16L7 15H3zM7 15l2 6h3l-2-6z"/></svg></div>
<div class="abs svc" style="left:469px;top:478px"><h3 class="h">Suchmaschinenwerbung</h3><p>Lorem ipsum dolor sit amet, consectetur adipiscing elit. Praesent eu nisi ac mi Ut egestas libero sit amet risus elementum rhoncus, elit id varius. <a>Mehr erfahren</a></p></div>

<div class="abs svc-icon" style="left:142px;top:545px"><svg width="12" height="12" viewBox="0 0 24 24" fill="#fff"><circle cx="12" cy="7" r="3.5"/><circle cx="5" cy="9" r="2.5"/><circle cx="19" cy="9" r="2.5"/><path d="M5 20c0-5 3-8 7-8s7 3 7 8zM1 18c0-3 2-5 4-5v5zM23 18c0-3-2-5-4-5v5z"/></svg></div>
<div class="abs svc" style="left:179px;top:548px"><h3 class="h">Social SEO</h3><p>Lorem ipsum dolor sit amet, consectetur adipiscing elit. Praesent eu nisi ac mi Ut egestas libero sit amet risus elementum rhoncus, elit id varius. <a>Mehr erfahren</a></p></div>
<div class="abs svc-icon" style="left:287px;top:545px"><svg width="11" height="11" viewBox="0 0 24 24" fill="#fff"><circle cx="12" cy="12" r="5"/></svg></div>
<div class="abs svc" style="left:324px;top:548px"><h3 class="h">Sucharo Penalty</h3><p>Lorem ipsum dolor sit amet, consectetur adipiscing elit. Praesent eu nisi ac mi Ut egestas libero sit amet risus elementum rhoncus, elit id varius. <a>Mehr erfahren</a></p></div>
<div class="abs svc-icon" style="left:432px;top:545px"><svg width="12" height="12" viewBox="0 0 24 24" fill="#fff"><path d="M2 6h14v12H2zM16 10l6-4v12l-6-4z"/></svg></div>
<div class="abs svc" style="left:469px;top:548px"><h3 class="h">Erklärvideos</h3><p>Lorem ipsum dolor sit amet, consectetur adipiscing elit. Praesent eu nisi ac mi Ut egestas libero sit amet risus elementum rhoncus, elit id varius. <a>Mehr erfahren</a></p></div>

<section class="abs cta">
  <h2 class="h" style="color:#fff">Nur die Top 10 zählen!</h2>
  <p>Mehr als 95% der Sucharo Nutzer schenken statistisch bewiesen lediglich den ersten 10 Positionen Beachtung.<br>Wie ist es bei Ihnen?</p>
</section>

<div class="abs col" style="left:142px;top:751px;width:131px">
  <h2 class="h"><strong>Was</strong> ist SEO?</h2>
  <p class="small" style="margin-top:5px">Nunc nunc dui, cursus eu risus et, venenatis semper orci. Integer congue auctor est at lacinia. Maecenas posuere nibh turpis, quis ornare purus mattis a. Integer felis nulla, auctor quis adipiscing a, consequat suscipit velit. Maecenas turpis Sed pharetra scelerisque dui.</p>
  <ul><li>Nullam porttitor, justo ut dignissim condimentum quis</li><li>Magna nulla aliquam mi, lobortis sagittis puru sapien</li><li>Suspendisse elementum, felis a tempus egestas turpi</li><li>Magna nulla aliquam mi, lobortis sagittis puru sapien</li></ul>
</div>
<a class="abs btn" style="left:142px;top:861px">Mehr erfahren</a>

<div class="abs col" style="left:287px;top:751px;width:131px">
  <h2 class="h"><strong>SEO</strong> (organisch)</h2>
  <p class="small" style="margin-top:5px">Nunc nunc dui, cursus eu risus et, venenatis semper orci. Integer congue auctor est at lacinia. Maecenas posuere nibh turpis, quis ornare purus mattis a. Integer felis nulla, auctor quis adipiscing a, consequat suscipit velit. Maecenas turpis Sed pharetra scelerisque dui.</p>
  <ul><li>Nullam porttitor, justo ut dignissim condimentum quis</li><li>Magna nulla aliquam mi, lobortis sagittis puru sapien</li><li>Suspendisse elementum, felis a tempus egestas turpi</li><li>Magna nulla aliquam mi, lobortis sagittis puru sapien</li></ul>
</div>
<a class="abs btn" style="left:287px;top:861px">Mehr erfahren</a>

<div class="abs col" style="left:432px;top:751px;width:134px">
  <h2 class="h"><strong>Unsere</strong> Garantie für Sie</h2>
  <p class="small" style="margin-top:5px">Sollten Ihre vorab festgelegten Suchbegriffe gegen alle Erwartungen nicht innerhalb von 6 Monaten unter den TOP 10 bei den Suchergebnissen von Sucharo gelistet sein, erhalten Sie von uns rückwirkend zu 100% Ihr Geld zurück - garantiert!<br>Testen Sie uns und lassen Sie sich von unserer Erfahrung und unserem Know-How beeindrucken.<br>Wir halten, was andere versprechen!</p>
  <ul><li class="h" style="font-size:7px;color:var(--ink)">100% Geld zurück Garantie</li></ul>
</div>
<a class="abs btn" style="left:432px;top:860px">Mehr erfahren</a>

<section class="abs quote">
  <svg class="abs" style="left:346px;top:18px" width="16" height="12" viewBox="0 0 16 12" fill="#ccc"><path d="M0 6C0 2 2 0 6 0v3C4 3 3.5 4 3.5 5H7v7H0zM9 6c0-4 2-6 6-6v3c-2 0-2.5 1-2.5 2H16v7H9z"/></svg>
  <blockquote>In vitae lacus consequat, commodo tortor sed, porttitor dolor. Morbi eu nisl ultrices, pulvinar ligula vitae, ullamcorper massa. Sed malesuada ut magna vitae scelerisque.</blockquote>
  <cite>— John Doe, Firma</cite>
  <div class="dots"><i class="on"></i><i></i><i></i></div>
</section>

<footer class="abs footer">
  <div class="abs" style="left:142px;top:17px">
    <h4>Übersicht</h4>
    <ul class="flinks"><li>Über uns</li><li>Kundenmeinungen</li><li>Kontakt</li><li>Whatever</li></ul>
  </div>
  <div class="abs" style="left:251px;top:17px;width:205px">
    <h4>Über uns</h4>
    <p class="ftext" style="margin-top:8px">Mauris et vulputate est. Integer viverra nunc vitae facilisis cursus. Quisque ac ultricies quam, a molestie leo. Nulla convallis turpis id vulputate aliquam. Nulla facilisi. Nam tincidunt odio dignissim dui lobortis adipiscing.</p>
    <p class="ftext" style="margin-top:7px">Nullam volutpat quis sem id iaculis. Fusce interdum, quam ac aliquam vulputate, orci nisl imperdiet turpis, non posuere massa ipsum et lorem. Pellentesque facilisis, orci nec gravida accumsan, massa elit hendrerit lacus, tortor.</p>
  </div>
  <div class="abs" style="left:468px;top:17px;width:100px">
    <h4>Kontaktieren Sie uns</h4>
    <div class="contact-row" style="margin-top:8px"><span class="ic"><svg width="5" height="6" viewBox="0 0 10 12" fill="#fff"><path d="M5 0a4 4 0 0 1 4 4c0 3-4 8-4 8S1 7 1 4a4 4 0 0 1 4-4z"/></svg></span><span>Beispielweg 12, 10115<br>Musterstadt</span></div>
    <div class="contact-row" style="margin-top:8px"><span class="ic"><svg width="5" height="5" viewBox="0 0 10 10" fill="#fff"><path d="M2 0l2 2-1 2c1 1 2 2 3 3l2-1 2 2-2 2C4 10 0 6 0 2z"/></svg></span><span>+49 30 555-0142<br>+49 30 555-0143</span></div>
    <div class="contact-row" style="margin-top:8px;color:#fff"><span class="ic"><svg width="6" height="4" viewBox="0 0 12 8" fill="#fff"><path d="M0 0h12L6 4zM0 1.5l6 4 6-4V8H0z"/></svg></span><span>info@klickretter.de</span></div>
  </div>
</footer>

<div class="abs bottombar">
  <span class="abs" style="left:142px;top:10px">© 2014 <b style="color:#fff;font-weight:600">klickretter.de</b></span>
  <span class="abs" style="left:438px;top:10px">Weitere Kontaktmöglichkeiten</span>
  <div class="abs fsoc socials" style="left:503px;top:8px"><i></i><i></i><i></i><i></i><i></i></div>
</div>

</body>
</html>
```